Music Studio and Store Business Card and Logo Design

We need a business card and logo design for an existing Music Studio (Piano and Voice) which will soon expand to offer retail sheet music for all instruments including voice. The expanding store will not sell or lease instruments. We are a well known Fine Arts Studio for instruction to children, college students, and adults with 42 enrolled students and a wait list. We want something with simple elegance, but not archaic. Even a sleek modern look is okay. We do not want something childish or too fun looking because we do serve ages 5 - 62. We would also like the logo workable/transferable to signage for our new location opening in March. We like classic burgundy, black, deep blues, but are open to other suggestions. We included our studio brochure so you can get to know us a little better and some images we thought were interesting with the use of clef signs for the & and using note heads for the bottom or top of the letter "H"

Target Market(s)

All ages

Industry/Entity Type

Business

Contact Information for Business Card

H&H Music StudioPlattsburgh, NYWanda J. Haby and Oren M. Castaldi, Owners

Requirements
Must have
• Phone Number: (555) 817-4062
• Website: www.rbtonalartsroom.example
Nice to have
• Email: lorna@rbtonalartsroom.example
Should not have
• Any instruments on the card other than piano. Instrument pix is not a necessity.

```html
<!DOCTYPE html>
<html lang="en">
<head>
<meta charset="utf-8">
<title>R&amp;B Music Studio – Business Cards</title>
<link rel="stylesheet" href="https://fonts.googleapis.com/css2?family=Cinzel:wght@600&family=Open+Sans:wght@400;600&display=swap">
<style>
  :root {
    --studio-red: #fb0a0a;
    --paper: #ffffff;
    --ink: #1a1a1a;
    --backdrop: #ece9e6;
  }
  * { margin: 0; padding: 0; box-sizing: border-box; }
  html, body { width: 1200px; height: 900px; overflow: hidden; }
  body { background: var(--backdrop); position: relative; font-family: "Open Sans", Arial, sans-serif; }

  .card {
    position: absolute;
    border-radius: 16px;
    overflow: hidden;
    box-shadow: 0 6px 18px rgba(0,0,0,0.18);
  }
  .card--front { left: 77px; top: 34px; width: 589px; height: 364px; background: var(--paper); }
  .card--back  { left: 389px; top: 507px; width: 565px; height: 348px; background: var(--studio-red); }

  .band { position: absolute; left: 0; right: 0; }
  .card--front .band { top: 48px; height: 99px; background: var(--studio-red); }
  .card--back .band  { top: 71px; height: 95px; background: var(--paper); }

  .emblem-disc { position: absolute; border-radius: 50%; }
  .card--front .emblem-disc { left: 218px; top: 18px; width: 156px; height: 156px; background: var(--paper); }
  .card--back .emblem-disc  { left: 202px; top: 38px; width: 160px; height: 160px; background: var(--studio-red); }

  .studio-name {
    position: absolute; left: 0; right: 0; text-align: center;
    font-family: "Cinzel", "Times New Roman", serif; font-weight: 600;
    letter-spacing: 1px; white-space: nowrap;
  }
  .card--front .studio-name { top: 180px; font-size: 38px; line-height: 48px; color: var(--studio-red); }
  .card--back .studio-name  { top: 203px; font-size: 42px; line-height: 54px; color: var(--paper); }

  .owners {
    position: absolute; left: 0; right: 0; top: 240px; text-align: center;
    font-weight: 600; font-size: 19px; line-height: 26px; color: var(--studio-red);
    white-space: nowrap;
  }
  .owners .divider { margin: 0 8px; }
  .role {
    position: absolute; left: 0; right: 0; top: 270px; text-align: center;
    font-size: 15px; line-height: 20px; color: var(--ink);
  }
  .location {
    position: absolute; left: 0; right: 0; top: 298px; text-align: center;
    font-size: 17px; line-height: 22px; color: var(--ink);
  }
  .contact {
    position: absolute; left: 0; right: 0; top: 326px; text-align: center;
    font-size: 14px; line-height: 20px; color: var(--ink); white-space: nowrap;
  }
  .contact .divider { margin: 0 8px; color: var(--studio-red); }
</style>
</head>
<body>
  <section class="card card--front" aria-label="Business card front">
    <div class="band"></div>
    <div class="emblem-disc"></div>
    <h1 class="studio-name">R&amp;B Music Studio</h1>
    <p class="owners">Lorna P. Quist<span class="divider">|</span>Oren M. Castaldi</p>
    <p class="role">Owners</p>
    <p class="location">Harlow Falls, NY</p>
    <p class="contact">(555) 817-4062<span class="divider">|</span>www.rbtonalartsroom.example</p>
  </section>

  <section class="card card--back" aria-label="Business card back">
    <div class="band"></div>
    <div class="emblem-disc"></div>
    <h2 class="studio-name">R&amp;B Music Studio</h2>
  </section>
</body>
</html>
```